BQR, LLC Original

I need a business card design for a new company in Gaithersburg, MD. Though the name of the company is Wiremasters Of Northfield (BQR) we specialize in commercial kitchen ventilation systems as a complete turnkey project or as a service provider. We can design the entire system including the hoods, fans, ductwork, and fire system. We also specialize in fire alarm service, design, install and inspection. We are experts on any Ventaro Dynamics equipment including Pulsar VXM, Pulsar Canopies, EMS controls, Standard controls, PCU filtration and Make-up Air units with heaters and cooling. We can repair/retrofit old water wash hood systems as well. We are experts with local code requirements and upgrades.

Industry/Entity Type

Business

Contact Information for Business Card

Dale Pruitt, Wiremasters Of Northfield, LLC; 240-555-0187 Cell, Larkspur Hill, MD 20999. Dalep@wiremastersnorthfield.example

```html
<!DOCTYPE html>
<html lang="en">
<head>
<meta charset="utf-8">
<title>Northfield, LLC – Business Card</title>
<link rel="stylesheet" href="https://fonts.googleapis.com/css2?family=Cinzel:wght@400&family=Arimo:wght@400&display=swap">
<style>
  :root {
    --backdrop: #9a5a34;
    --card-white: #ffffff;
    --panel-dark: #262626;
    --panel-dark-2: #1b1b1b;
    --rule-black: #000000;
    --band-navy: #111624;
    --accent-orange: #f29a1f;
    --accent-yellow: #e6c21a;
    --text-light: #f2f2f2;
  }
  html, body {
    margin: 0;
    padding: 0;
    width: 1200px;
    height: 914px;
    overflow: hidden;
    background: var(--backdrop);
  }
  .canvas {
    position: relative;
    width: 1200px;
    height: 914px;
  }
  .card {
    position: absolute;
    width: 620px;
    height: 354px;
    background: var(--card-white);
    box-shadow: 0 6px 18px rgba(0,0,0,0.28);
    overflow: hidden;
  }
  .card--front { left: 70px; top: 70px; }
  .card--back { left: 510px; top: 490px; }

  /* Front */
  .front-shape {
    position: absolute;
    inset: 0;
    width: 100%;
    height: 100%;
  }
  .brand {
    position: absolute;
    left: 28px;
    top: 48px;
    width: 250px;
    text-align: center;
  }
  .brand__mark {
    display: block;
    width: 124px;
    height: 124px;
    margin: 0 auto 18px;
    border-radius: 50%;
    background: #000;
  }
  .brand__name {
    font-family: "Cinzel", serif;
    font-size: 22px;
    color: var(--accent-orange);
    letter-spacing: 0.5px;
  }
  .person {
    position: absolute;
    right: 34px;
    top: 112px;
    text-align: right;
    color: var(--text-light);
  }
  .person__name {
    font-family: "Cinzel", serif;
    font-size: 21px;
    letter-spacing: 0.5px;
  }
  .person__role {
    font-family: "Arimo", sans-serif;
    font-size: 15px;
    margin-top: 2px;
  }
  .divider {
    position: absolute;
    right: 60px;
    top: 185px;
    width: 200px;
    height: 2px;
    background: var(--text-light);
  }
  .contacts {
    position: absolute;
    right: 34px;
    top: 232px;
    margin: 0;
    padding: 0;
    list-style: none;
    font-family: "Arimo", sans-serif;
    font-size: 15px;
    color: var(--text-light);
    text-align: right;
  }
  .contacts__item {
    display: flex;
    justify-content: flex-end;
    align-items: center;
    gap: 10px;
    height: 24px;
  }
  .contacts__icon {
    width: 17px;
    height: 15px;
    border-radius: 2px;
    background: var(--accent-orange);
    flex: none;
  }
  .contacts__icon svg { display: block; width: 17px; height: 15px; }

  /* Back */
  .band {
    position: absolute;
    left: 0;
    right: 0;
    top: 78px;
    height: 72px;
    background: var(--band-navy);
    display: flex;
    align-items: center;
    justify-content: center;
  }
  .band__name {
    font-family: "Cinzel", serif;
    font-size: 24px;
    color: var(--accent-yellow);
    letter-spacing: 0.5px;
  }
</style>
</head>
<body>
<main class="canvas">

  <section class="card card--front" aria-label="Business card front">
    <svg class="front-shape" viewBox="0 0 620 354" preserveAspectRatio="none" aria-hidden="true">
      <defs>
        <linearGradient id="panelShade" x1="0" y1="0" x2="1" y2="1">
          <stop offset="0" stop-color="#2e2e2e"/>
          <stop offset="1" stop-color="#1a1a1a"/>
        </linearGradient>
      </defs>
      <polyline points="286,0 338,212 160,354" fill="none" stroke="#000" stroke-width="4"/>
      <polygon points="298,0 620,0 620,354 176,354 350,214" fill="url(#panelShade)"/>
    </svg>

    <div class="brand">
      <span class="brand__mark"></span>
      <div class="brand__name">Northfield, LLC</div>
    </div>

    <div class="person">
      <div class="person__name">Dale Pruitt</div>
      <div class="person__role">Electricians</div>
    </div>

    <div class="divider"></div>

    <ul class="contacts">
      <li class="contacts__item">240-555-0187
        <span class="contacts__icon"><svg viewBox="0 0 17 15"><path d="M5 3c1 0 1.5 2 1 2.6L5.3 6.5c.8 1.6 2 2.8 3.4 3.5l.9-.8c.6-.5 2.6 0 2.6 1 0 .9-.8 1.8-1.8 1.8C7 12 4 9 3.2 5 3.2 4 4 3 5 3z" fill="#fff"/></svg></span>
      </li>
      <li class="contacts__item">Larkspur Hill, MD 20999.
        <span class="contacts__icon"><svg viewBox="0 0 17 15"><path d="M8.5 2.5a3.5 3.5 0 0 1 3.5 3.5c0 2.5-3.5 6.5-3.5 6.5S5 8.5 5 6a3.5 3.5 0 0 1 3.5-3.5z" fill="#fff"/><circle cx="8.5" cy="6" r="1.3" fill="#f29a1f"/></svg></span>
      </li>
      <li class="contacts__item">Dalep@wiremastersnorthfield.example
        <span class="contacts__icon"><svg viewBox="0 0 17 15"><rect x="3.5" y="4" width="10" height="7" fill="#fff"/><path d="M3.5 4l5 4 5-4" fill="none" stroke="#f29a1f" stroke-width="1"/></svg></span>
      </li>
    </ul>
  </section>

  <section class="card card--back" aria-label="Business card back">
    <div class="band">
      <div class="band__name">Northfield, LLC</div>
    </div>
  </section>

</main>
</body>
</html>
```